Brimlow Plumbing Solutions

This is for my new plumbing company, I have attached an example of what I’m going for but want it to look better.

Target Market(s)

Home owners, real estate, etc.

Industry/Entity Type

Plumbing

Font styles to use
Other font styles liked:
• As per my logo and other examples uploaded

Colors

Designer to choose colors to be used in the design.

Requirements
Must have
• Must include my logo provided and similar to my flyer I have attached but better

```html
<!DOCTYPE html>
<html lang="en">
<head>
<meta charset="UTF-8">
<title>Brimlow Plumbing Solutions – Flyer</title>
<link href="https://fonts.googleapis.com/css2?family=Inter:wght@400;500;600;700&display=swap" rel="stylesheet">
<style>
  :root {
    --navy: #15305f;
    --navy-deep: #102650;
    --sky: #4f9fd8;
    --sky-light: #6cb3e4;
    --water-1: #2f6fb3;
    --water-2: #9cc7ea;
    --brass-1: #8a7a5c;
    --brass-2: #c9d6e3;
    --white: #ffffff;
    --ink: #1b2f55;
    --muted: #7c8797;
    --orange: #f47a20;
    --page: #e9ebee;
    --card-line: #e3e8ef;
  }
  * { box-sizing: border-box; margin: 0; padding: 0; }
  html, body {
    width: 1200px; height: 1200px; overflow: hidden;
    background: var(--page);
    font-family: "Inter", Arial, sans-serif;
  }
  .flyer {
    position: absolute; left: 260px; top: 100px;
    width: 680px; height: 1000px;
    background: var(--white);
    overflow: hidden;
  }
  .flyer-top { position: absolute; left: 0; top: 0; }
  .brand {
    position: absolute; left: 0; top: 34px; width: 680px;
    display: flex; justify-content: center; align-items: center; gap: 10px;
    color: var(--white); font-weight: 600;
  }
  .brand-dot { width: 30px; height: 30px; border-radius: 50%; background: var(--white); }
  .brand-name { line-height: 1.05; }
  .brand-name .line-main { display: block; font-size: 30px; letter-spacing: 0.5px; }
  .brand-name .line-sub { display: block; font-size: 14px; }
  .tagline {
    position: absolute; left: 42px; top: 330px;
    color: var(--white); font-size: 22px; font-weight: 500;
  }
  .services-title {
    position: absolute; left: 43px; top: 398px;
    color: var(--ink); font-size: 26px; font-weight: 600;
  }
  .service-grid {
    position: absolute; left: 43px; top: 445px;
    display: grid; grid-template-columns: repeat(4, 140px);
    grid-auto-rows: 126px; gap: 16px 12px;
  }
  .service-card {
    background: var(--white);
    border: 1px solid var(--card-line);
    box-shadow: 0 2px 6px rgba(21, 48, 95, 0.12);
    padding: 12px 10px 8px;
    text-align: center;
  }
  .service-icon { width: 26px; height: 26px; display: block; margin: 0 auto 8px; }
  .service-name { color: var(--ink); font-size: 15px; font-weight: 600; line-height: 1.2; }
  .service-card.left .service-name, .service-card.left .service-text { text-align: left; }
  .service-text { color: var(--muted); font-size: 8.5px; line-height: 1.35; margin-top: 7px; }
  .offer { position: absolute; left: 0; top: 740px; }
  .offer-copy {
    position: absolute; left: 42px; top: 763px;
    color: var(--white); font-size: 25px; font-weight: 500; line-height: 1.25;
  }
  .offer-copy .highlight { color: var(--orange); }
  .badge { position: absolute; left: 510px; top: 756px; width: 120px; height: 120px; }
  .badge-text {
    position: absolute; left: 510px; top: 798px; width: 120px;
    text-align: center; color: var(--white); font-size: 13px; font-weight: 700; line-height: 1.15;
  }
  .footer {
    position: absolute; left: 0; top: 875px; width: 680px; height: 125px;
    background: var(--sky);
  }
  .contact-row {
    position: absolute; left: 42px; display: flex; align-items: center; gap: 22px;
    color: var(--white); font-size: 13px;
  }
  .contact-row.first { top: 36px; }
  .contact-row.second { top: 64px; }
  .contact-item { display: flex; align-items: center; gap: 6px; }
  .contact-icon { width: 15px; height: 15px; }
  .social { position: absolute; left: 506px; top: 36px; display: flex; gap: 6px; }
  .social-dot { width: 15px; height: 15px; border-radius: 50%; background: var(--navy); }
</style>
</head>
<body>
<main class="flyer">
  <svg class="flyer-top" width="680" height="380" viewBox="0 0 680 380">
    <defs>
      <linearGradient id="gDrop" x1="0" y1="0" x2="1" y2="1">
        <stop offset="0" stop-color="var(--water-2)"/><stop offset="1" stop-color="var(--water-1)"/>
      </linearGradient>
      <linearGradient id="gFlow" x1="0" y1="0" x2="0" y2="1">
        <stop offset="0" stop-color="#d7e6f2"/><stop offset="1" stop-color="#7fa9cf"/>
      </linearGradient>
      <linearGradient id="gTap" x1="0" y1="0" x2="1" y2="1">
        <stop offset="0" stop-color="var(--brass-2)"/><stop offset="1" stop-color="var(--brass-1)"/>
      </linearGradient>
      <linearGradient id="gBeads" x1="0" y1="0" x2="1" y2="1">
        <stop offset="0" stop-color="#8cc0e8"/><stop offset="1" stop-color="#4a8fcf"/>
      </linearGradient>
    </defs>
    <rect class="header-band" x="0" y="0" width="680" height="130" fill="var(--navy)"/>
    <polygon points="0,58 120,58 150,129 0,129" fill="var(--sky)"/>
    <polygon points="590,74 680,74 680,129 560,129" fill="var(--sky)"/>
    <polygon role="img" aria-label="Photo of a water droplet splashing into blue water" points="0,129 210,129 150,310 0,310" fill="url(#gDrop)"/>
    <polygon role="img" aria-label="Photo of water running from a chrome tap into a basin" points="218,129 360,129 300,310 158,310" fill="url(#gFlow)"/>
    <polygon role="img" aria-label="Photo of a brass garden tap with running water" points="368,129 560,129 500,310 308,310" fill="url(#gTap)"/>
    <polygon role="img" aria-label="Photo of water beads on a blue surface" points="568,129 680,129 680,310 508,310" fill="url(#gBeads)"/>
    <polygon class="tagline-band" points="0,310 500,310 470,378 0,378" fill="var(--navy)"/>
    <polygon points="508,310 680,310 680,378 478,378" fill="var(--sky)"/>
  </svg>

  <div class="brand">
    <span class="brand-dot"></span>
    <span class="brand-name"><span class="line-main">BRIMLOW</span><span class="line-sub">Plumbing Solutions</span></span>
  </div>

  <p class="tagline">Reliable Plumbing. Real Solutions</p>

  <h2 class="services-title">Our Services</h2>

  <section class="service-grid">
    <article class="service-card left">
      <svg class="service-icon" viewBox="0 0 26 26" fill="none" stroke="var(--navy)" stroke-width="1.6"><path d="M4 10h12v4H4zM10 6v4M7 6h6M16 12h4v6"/></svg>
      <h3 class="service-name">Emergency Plumbing</h3>
      <p class="service-text">Fast response for bursts and urgent leaks.</p>
    </article>
    <article class="service-card">
      <svg class="service-icon" viewBox="0 0 26 26" fill="none" stroke="var(--navy)" stroke-width="1.6"><circle cx="8" cy="9" r="3"/><circle cx="18" cy="9" r="3"/><path d="M10 17l3 3 3-3"/></svg>
      <h3 class="service-name">Plumbing Maintenance</h3>
      <p class="service-text">Routine checks to keep pipes running well.</p>
    </article>
    <article class="service-card">
      <svg class="service-icon" viewBox="0 0 26 26" fill="none" stroke="var(--navy)" stroke-width="1.6"><path d="M8 22V6h6v4M6 22h14M16 14v8"/></svg>
      <h3 class="service-name">Drainage Maintenance</h3>
      <p class="service-text">Clear, clean drains inspected and serviced.</p>
    </article>
    <article class="service-card">
      <svg class="service-icon" viewBox="0 0 26 26" fill="none" stroke="var(--navy)" stroke-width="1.6"><rect x="7" y="5" width="12" height="16" rx="3"/><path d="M13 9v6"/></svg>
      <h3 class="service-name" style="font-size:13px">Hot Water Systems</h3>
      <p class="service-text">Repairs and installs for all hot water units.</p>
    </article>
    <article class="service-card left">
      <svg class="service-icon" viewBox="0 0 26 26" fill="none" stroke="var(--navy)" stroke-width="1.6"><rect x="5" y="5" width="16" height="12"/><path d="M9 17v4M17 17v4M5 21h16"/></svg>
      <h3 class="service-name" style="font-size:14px">Leaking Fixtures</h3>
      <p class="service-text">Dripping fixtures found and fixed for good.</p>
    </article>
    <article class="service-card">
      <svg class="service-icon" viewBox="0 0 26 26" fill="none" stroke="var(--navy)" stroke-width="1.6"><path d="M11 4c0 4-4 7-4 11a4 4 0 0 0 8 0c0-4-4-7-4-11zM17 12h4v9h-4"/></svg>
      <h3 class="service-name">Leaking</h3>
      <p class="service-text">Quick repairs for taps, pipes and joins.</p>
    </article>
    <article class="service-card">
      <svg class="service-icon" viewBox="0 0 26 26" fill="none" stroke="var(--navy)" stroke-width="1.6"><path d="M5 20l9-9M14 11l4-4 3 3-4 4zM8 6h3M6 9h2"/></svg>
      <h3 class="service-name" style="font-size:14px">Blocked Sewer &amp; Stormwater</h3>
      <p class="service-text">Blockages cleared from sewer and stormwater lines.</p>
    </article>
    <article class="service-card">
      <svg class="service-icon" viewBox="0 0 26 26" fill="none" stroke="var(--navy)" stroke-width="1.6"><circle cx="11" cy="12" r="6"/><path d="M8 10l6 4M15 16l5 5"/></svg>
      <h3 class="service-name" style="font-size:14px">Camera &amp; Locating TMV Maintenance</h3>
    </article>
  </section>

  <svg class="offer" width="680" height="135" viewBox="0 0 680 135">
    <rect x="0" y="0" width="680" height="135" rx="14" fill="var(--navy)"/>
    <rect x="0" y="60" width="680" height="75" fill="var(--navy)"/>
    <polygon points="405,0 418,0 478,135 440,135" fill="var(--sky-light)"/>
    <polygon points="418,0 426,0 486,135 478,135" fill="var(--white)"/>
  </svg>
  <p class="offer-copy">Discount information<br>Mention this flyer to receive<br><span class="highlight">15%</span> off your first service</p>
  <svg class="badge" viewBox="0 0 120 120">
    <polygon fill="var(--orange)" stroke="var(--white)" stroke-width="2.5" points="116,60 108.1,69.6 111.7,81.4 100.7,87.2 99.6,99.6 87.2,100.7 81.4,111.7 69.6,108.1 60,116 50.4,108.1 38.6,111.7 32.8,100.7 20.4,99.6 19.3,87.2 8.3,81.4 11.9,69.6 4,60 11.9,50.4 8.3,38.6 19.3,32.8 20.4,20.4 32.8,19.3 38.6,8.3 50.4,11.9 60,4 69.6,11.9 81.4,8.3 87.2,19.3 99.6,20.4 100.7,32.8 111.7,38.6 108.1,50.4"/>
  </svg>
  <p class="badge-text">DISCOUNT<br>HIGHLIGHT</p>

  <footer class="footer">
    <div class="contact-row first">
      <span class="contact-item">
        <svg class="contact-icon" viewBox="0 0 16 16" fill="var(--white)"><path d="M4 1.5l2.2 3-1.3 1.6a8 8 0 0 0 5 5l1.6-1.3 3 2.2-1.3 2.3C7.5 14.2 1.8 8.5 1.7 2.8z"/></svg>
        0400 555 218
      </span>
    </div>
    <div class="contact-row second">
      <span class="contact-item">
        <svg class="contact-icon" viewBox="0 0 16 16" fill="none" stroke="var(--white)" stroke-width="1.4"><rect x="1.5" y="3.5" width="13" height="9"/><path d="M1.5 3.5l6.5 5 6.5-5"/></svg>
        brimlowplumbingsolutions.com
      </span>
      <span class="contact-item">
        <svg class="contact-icon" viewBox="0 0 16 16" fill="none" stroke="var(--white)" stroke-width="1.4"><circle cx="8" cy="8" r="6.5"/><path d="M1.5 8h13M8 1.5c3 3.5 3 9.5 0 13M8 1.5c-3 3.5-3 9.5 0 13"/></svg>
        brimlowplumbing.com.au
      </span>
      <span class="contact-item">
        <svg class="contact-icon" viewBox="0 0 16 16" fill="none" stroke="var(--white)" stroke-width="1.4"><rect x="2" y="2" width="12" height="12" rx="2"/></svg>
        @BrimlowPlumbingSolutions
      </span>
    </div>
    <div class="social"><span class="social-dot"></span><span class="social-dot"></span></div>
  </footer>
</main>
</body>
</html>
```